Naturopath Practitioner Card Design

I am a naturopath needing a design for a business card mainly to show that I am a naturopath and have some contact details to give to prospective clients. I am open minded about the design and what is on the second side of the card whether it just be some artwork or space for details, appointment times etc. Naturopathy is the practice of natural medicine that uses a holistic approach and incorporates herbal and nutritional medicine.

Industry/Entity Type

Business

Contact Information for Business Card

Tom Rudd NaturopathBHSc (Naturopathy) Member WHPG 0487 925 316 tom.rudd@mailexample.com www.tomruddnaturopathy.example.au

Requirements
Nice to have
• Would prefer some kind of original pattern/art work/logo rather than an image, not fussed if its very simple/basic
• I am open to any colour but think I would prefer a more earthy sandy clay etc type style than the greens that are commonly associated with naturopathy.
Should not have
• Don't really want to have generic stock images on it

```html
<!DOCTYPE html>
<html lang="en">
<head>
<meta charset="utf-8">
<title>Tom Rudd Naturopathy – Business Card</title>
<link rel="stylesheet" href="https://fonts.googleapis.com/css2?family=Open+Sans:wght@400;600;700&display=swap">
<style>
  :root {
    --leaf: #6a8a3a;
    --ink: #2f2f2f;
    --ink-soft: #3d3d3d;
    --paper: #ffffff;
    --backdrop: #ebe8e3;
    --rule: #222222;
  }
  * { box-sizing: border-box; margin: 0; padding: 0; }
  html, body { width: 1200px; height: 1000px; overflow: hidden; }
  body {
    background: var(--backdrop);
    font-family: "Open Sans", Arial, sans-serif;
    color: var(--ink);
    position: relative;
  }
  .card {
    position: absolute;
    left: 265px;
    width: 666px;
    height: 397px;
    background: var(--paper);
    box-shadow: 0 2px 8px rgba(0,0,0,0.18);
  }
  .card--front { top: 73px; }
  .card--back { top: 533px; }

  /* Front */
  .brand {
    position: absolute; left: 0; right: 0; top: 60px;
    text-align: center;
  }
  .brand__mark {
    display: block; margin: 0 auto 22px;
    width: 70px; height: 70px; border-radius: 50%;
    background: var(--leaf);
  }
  .brand__name {
    font-size: 40px; font-weight: 400; color: var(--ink-soft);
    letter-spacing: 1px; line-height: 1.2;
  }
  .practitioner {
    position: absolute; left: 0; right: 0; top: 265px;
    text-align: center; color: var(--leaf); font-size: 18px;
  }
  .practitioner__name { font-weight: 700; font-size: 20px; }
  .divider {
    width: 240px; height: 1px; margin: 8px auto 4px;
    background: linear-gradient(90deg, transparent, #9a9a9a, transparent);
  }
  .membership {
    font-size: 16px; color: var(--ink); text-align: center;
  }
  .contacts {
    position: absolute; left: 0; right: 0; top: 336px;
    display: flex; justify-content: center; gap: 18px;
    font-size: 15px; color: var(--ink);
  }
  .contact { display: flex; align-items: center; gap: 6px; white-space: nowrap; }
  .contact svg { width: 15px; height: 15px; fill: var(--leaf); }
  .band-bottom {
    position: absolute; left: 0; right: 0; bottom: 0; height: 25px;
    background: var(--leaf);
  }

  /* Back */
  .band-top {
    position: absolute; left: 0; right: 0; top: 0; height: 47px;
    background: var(--leaf); color: #fff;
    font-size: 18px; font-weight: 600;
    display: flex; align-items: center; justify-content: center;
  }
  .field-line {
    position: absolute; left: 133px; width: 400px; height: 1.5px;
    background: var(--rule);
  }
  .field-line--for { top: 144px; }
  .field-line--when { top: 286px; }
  .label {
    position: absolute; font-size: 16px; color: var(--ink);
    transform: translateX(-50%);
  }
  .label--for { left: 333px; top: 154px; }
  .label--date { left: 247px; top: 296px; }
  .label--time { left: 421px; top: 296px; }
  .days {
    position: absolute; left: 33px; right: 28px; top: 212px;
    display: flex; justify-content: space-between;
    font-size: 16px; color: var(--ink);
  }
  .day { display: flex; align-items: center; gap: 12px; }
  .day__box {
    width: 15px; height: 15px; border: 2px solid var(--leaf);
  }
  .notice {
    position: absolute; left: 0; right: 0; top: 346px;
    text-align: center; font-size: 16.5px; color: var(--ink);
  }
</style>
</head>
<body>

<section class="card card--front">
  <div class="brand">
    <span class="brand__mark"></span>
    <div class="brand__name">Tom Rudd Naturopathy</div>
  </div>

  <div class="practitioner">
    <span class="practitioner__name">Tom Rudd</span> BHSc (Naturopathy)
    <div class="divider"></div>
    <div class="membership">Member WHPG</div>
  </div>

  <div class="contacts">
    <span class="contact">
      <svg viewBox="0 0 16 16" aria-hidden="true"><path d="M1 3h14v10H1z M1 3l7 6 7-6" fill="var(--leaf)"/><path d="M1.5 3.5l6.5 5.5 6.5-5.5" fill="none" stroke="#fff" stroke-width="1.2"/></svg>
      tom.rudd@mailexample.com
    </span>
    <span class="contact">
      <svg viewBox="0 0 16 16" aria-hidden="true"><path d="M3.5 1.5l2.5 0.5 1 3-1.8 1.3c0.9 1.9 2.4 3.4 4.3 4.3L10.8 8.8l3 1 0.5 2.5-1.8 2C6.5 14 2 9.5 1.7 3.3z"/></svg>
      0487 925 316
    </span>
    <span class="contact">
      <svg viewBox="0 0 16 16" aria-hidden="true"><circle cx="8" cy="8" r="7"/><path d="M1 8h14M8 1c-3 3-3 11 0 14M8 1c3 3 3 11 0 14" fill="none" stroke="#fff" stroke-width="1"/></svg>
      tomruddnaturopathy.example.au
    </span>
  </div>

  <div class="band-bottom"></div>
</section>

<section class="card card--back">
  <div class="band-top">NEXT APPOINTMENT</div>

  <div class="field-line field-line--for"></div>
  <span class="label label--for">FOR</span>

  <div class="days">
    <span class="day">MON <span class="day__box"></span></span>
    <span class="day">TUE <span class="day__box"></span></span>
    <span class="day">WED <span class="day__box"></span></span>
    <span class="day">THUR <span class="day__box"></span></span>
    <span class="day">FRI <span class="day__box"></span></span>
    <span class="day">SAT <span class="day__box"></span></span>
  </div>

  <div class="field-line field-line--when"></div>
  <span class="label label--date">DATE</span>
  <span class="label label--time">TIME</span>

  <p class="notice">If you are unable to keep your appointment , please allow 24 hours notice</p>
</section>

</body>
</html>
```